Business card design needed

Front of Card:
I would like to have nearly 3/4 of the card from the top in a Pea Green Colour with the word 'Brambleway' written in a(Watermelon Red colour) in the font 'Viner Hand ITC'. Brambleway to be written within the Green colour of the card.

The lower 1/3 of the card I would like to have white with the words:
Home and Garden Styling smaller than the word Brambleway in Black in the font 'Batang', centred underneath the green section.

At the very bottom in one corner in smaller print I would like to have my contact phone number: Pia M:0437619204 and then the email address:
E: brambleaystudio@kelnor.net.au on the other side.

Back of Card:
Back of Card to be White
On one side (Left)
I would like the Heading "Garden" in the same pea green colour as the front and in the Viner Hand ITC font. On the other half of the card I would like 'Home' in the Watermelon Red Colour (same as front colour) and in the font Viner Hand ITC.
Underneath these Headings I would like written in black and in Batang font the following list of services.

Garden Home
Garden Styling Interior Styling
Plant Selection Furniture Selection/Arrangement Garden Maintenance Setting Up Home (after move)
Hedging/Mowing Merchandise and Stylist for
Work w/Local Nurseries Marrow and Finch

Brambleway
Home and Garden Styling
M: 0437619204 E: brambleaystudio@kelnor.net.au

```html
<!DOCTYPE html>
<html lang="en">
<head>
<meta charset="utf-8">
<title>Brambleway – Business Card</title>
<link rel="stylesheet" href="https://fonts.googleapis.com/css2?family=Gowun+Batang&family=Kalam:wght@700&display=swap">
<style>
  :root {
    --backdrop: #e6e6e6;
    --card: #ffffff;
    --card-edge: #c9c9c9;
    --pea-green: #1f9a06;
    --watermelon: #f7368f;
    --watermelon-deep: #ff1a6e;
    --ink: #111111;
    --font-script: "Kalam", cursive;
    --font-serif: "Gowun Batang", serif;
  }
  * { box-sizing: border-box; margin: 0; padding: 0; }
  html, body { width: 1063px; height: 1200px; overflow: hidden; background: var(--backdrop); }
  .canvas { position: relative; width: 1063px; height: 1200px; }

  .card {
    position: absolute;
    background: var(--card);
    border: 1px solid var(--card-edge);
    box-shadow: 4px 6px 14px rgba(0,0,0,0.18);
    overflow: hidden;
  }

  /* Front */
  .card--front { left: 79px; top: 89px; width: 875px; height: 486px; }
  .front__band {
    position: absolute; left: 0; top: 0; width: 100%; height: 314px;
    background: var(--pea-green);
    display: flex; align-items: center; justify-content: center;
  }
  .front__name {
    font-family: var(--font-script);
    font-weight: 700;
    font-size: 150px;
    line-height: 1;
    color: var(--watermelon);
    margin-top: 10px;
  }
  .front__tagline {
    position: absolute; left: 0; right: 0; top: 318px;
    text-align: center;
    font-family: var(--font-serif);
    font-size: 56px;
    color: var(--ink);
  }
  .front__contacts {
    position: absolute; top: 414px; left: 88px;
    display: flex; gap: 58px;
    font-family: var(--font-serif);
    font-size: 27px;
    color: var(--ink);
  }
  .contact { display: flex; align-items: center; gap: 8px; }
  .contact svg { flex: none; }

  /* Back */
  .card--back { left: 75px; top: 609px; width: 875px; height: 486px; }
  .services {
    position: absolute; top: 62px;
    font-family: var(--font-serif);
    color: var(--ink);
  }
  .services--garden { left: 86px; }
  .services--home { left: 454px; }
  .services__heading {
    font-family: var(--font-script);
    font-weight: 700;
    font-size: 56px;
    line-height: 1.2;
    margin-left: 10px;
    margin-bottom: 58px;
  }
  .services--garden .services__heading { color: var(--pea-green); }
  .services--home .services__heading { color: var(--watermelon-deep); }
  .services__list { list-style: none; font-size: 24px; line-height: 37.5px; }
  .services__list li { position: relative; padding-left: 20px; }
  .services__list li::before {
    content: ""; position: absolute; left: 0; top: 15px;
    width: 8px; height: 8px; border-radius: 50%;
  }
  .services--garden li::before { background: var(--pea-green); }
  .services--home li::before { background: var(--watermelon-deep); }

  .back__stripe { position: absolute; left: 0; bottom: 0; width: 100%; height: 30px; }
</style>
</head>
<body>
<main class="canvas">

  <section class="card card--front" aria-label="Business card front">
    <div class="front__band">
      <h1 class="front__name">Brambleway</h1>
    </div>
    <p class="front__tagline">Home and Garden Styling</p>
    <div class="front__contacts">
      <span class="contact">
        <svg width="18" height="24" viewBox="0 0 18 24" aria-hidden="true">
          <path d="M5 1 L8 7 L5.5 9 Q7 15 11 18.5 L13.5 16.5 L17 21.5 L13.5 23.5 Q4 20 1.5 6 Z" fill="none" stroke="var(--ink)" stroke-width="2" stroke-linejoin="round"/>
        </svg>
        0437619204
      </span>
      <span class="contact">
        <svg width="26" height="20" viewBox="0 0 26 20" aria-hidden="true">
          <rect x="1" y="3" width="24" height="15" fill="none" stroke="var(--ink)" stroke-width="1.6"/>
          <path d="M1 3 L13 12 L25 3 M1 18 L10 10 M25 18 L16 10" fill="none" stroke="var(--ink)" stroke-width="1.6"/>
        </svg>
        brambleaystudio@kelnor.net.au
      </span>
    </div>
  </section>

  <section class="card card--back" aria-label="Business card back">
    <div class="services services--garden">
      <h2 class="services__heading">Garden</h2>
      <ul class="services__list">
        <li>Garden Styling</li>
        <li>Plant Selection</li>
        <li>Garden Maintenance</li>
        <li>Hedging/Mowing</li>
        <li>Work w/Local Nurseries</li>
      </ul>
    </div>
    <div class="services services--home">
      <h2 class="services__heading">Home</h2>
      <ul class="services__list">
        <li>Interior Styling</li>
        <li>Furniture Selection/Arrangement</li>
        <li>Setting Up Home (after move)</li>
        <li>Merchandise and Stylist<br>for Marrow &amp; Finch</li>
      </ul>
    </div>
    <svg class="back__stripe" viewBox="0 0 875 30" preserveAspectRatio="none" aria-hidden="true">
      <rect width="875" height="30" fill="var(--watermelon-deep)"/>
      <polygon points="0,0 466,0 419,30 0,30" fill="var(--pea-green)"/>
    </svg>
  </section>

</main>
</body>
</html>
```